Homeowners Insurance Provider Website

We are selling homeowners insurance policy / tenants Policy/Flood Insurance in USA in few states and planning expand nationally.

Our target audience are two folds: Customers (Buy policies) and Insurance Agents who wants to work with us to sell our policies to customers. But website should focus 80% on customers and 20% on agents. So, more customer focused user experience. Please note that there is no direct buy option for customers. They always go through insurance agents.

Customer focused, educational that makes buyer journey easy. We don’t want to come off as trying sell something as there is no direct sales involved from website.

Target Market(s)

Homeowners in USA and Insurance agent who sells these insurance.

Industry/Entity Type

Insurance

Number of Pages Required

4 page

Font styles to use
Other font styles liked:
• Open to suggestions

Colors

Designer to choose colors to be used in the design.

Requirements
Must have
• Three most important things: Trustworthy, Authentic, Simple
• Please use colors form logo and grays
• We like: www.hollowmere.com
• https://www.quillfenbrook.com/
• We need Agent Look up tool on home page similar to what is shown on example sites.
• Design:
• Home Page - Open to Ideas
• Insurance (Products) Landing Page - Info similar to: https://www.quillfenbrook.com/insurance/
• Agents Page - https://www.quillfenbrook.com/agents/
• Claims Page - Information similar to: https://www.quillfenbrook.com/claims-center/
• Site Navigation:
• Home
• Insurance
• Claims
• Agents
• About Us
• Contact Us
Nice to have
• Elegant, minimal and clean design that reflects trust and authenticity.
Should not have
• Slider or rotating images - prefer flat design. Not over powering design.

```html
<!DOCTYPE html>
<html lang="en">
<head>
<meta charset="utf-8">
<title>Claims Center – Hearthward Insurance Co.</title>
<link href="https://fonts.googleapis.com/css2?family=Source+Sans+3:wght@400;600;700&family=Urbanist:wght@600;700&display=swap" rel="stylesheet">
<style>
:root{
  --navy:#1b3a83;
  --navy-dark:#142f73;
  --blue:#1f5aab;
  --red:#dc2127;
  --ink:#1c1c1c;
  --text:#4a4a4a;
  --muted:#666;
  --panel:#f5f6f8;
  --line:#e4e6ea;
  --footer:#353a43;
  --footer-text:#c3c7ce;
  --white:#fff;
}
*{box-sizing:border-box;margin:0;padding:0}
html,body{width:903px;height:1200px;overflow:hidden;background:var(--white)}
body{position:relative;font-family:"Source Sans 3",sans-serif;color:var(--text)}
.abs{position:absolute}
h1,h2{font-family:"Urbanist",sans-serif;font-weight:700;color:var(--ink)}
a{text-decoration:none;color:inherit}

/* header */
.site-header{left:0;top:0;width:903px;height:56px;background:var(--white)}
.brand{left:130px;top:11px;display:flex;align-items:center;gap:8px}
.brand-mark{width:26px;height:26px;border-radius:50%;background:var(--navy)}
.brand-name{font-family:"Source Sans 3",sans-serif;font-weight:700;font-size:14px;line-height:14px;color:var(--navy);letter-spacing:.3px}
.brand-name small{display:block;font-size:9px;font-weight:700;letter-spacing:1.6px}
.main-nav{left:334px;top:21px;display:flex;gap:13.5px;font-size:10px;font-weight:600;color:#333}
.main-nav .active{color:var(--red)}
.btn-top{top:15px;height:25px;display:flex;align-items:center;justify-content:center;gap:4px;font-size:10px;font-weight:600;color:var(--white)}
.btn-careers{left:640px;width:65px;background:var(--navy)}
.btn-login{left:708px;width:65px;background:var(--red)}

/* hero */
.hero{left:0;top:56px;width:903px;height:339px;background:linear-gradient(90deg,#fbfbfc 0%,#f2f4f7 45%,#dfe6ec 100%)}
.hero-photo{left:410px;top:0;width:493px;height:339px;background:linear-gradient(100deg,rgba(240,243,246,0) 0%,#cfd6dc 35%,#a9a097 65%,#c7ced5 100%)}
.hero h1{position:absolute;left:129px;top:76px;font-size:21px}
.hero p{position:absolute;left:129px;top:104px;width:300px;font-size:11px;line-height:17px;color:#444}

/* claim panels */
.panel{top:395px;height:174px;background:var(--panel)}
.panel-report{left:0;width:452px;border-right:1px solid var(--line)}
.panel-view{left:452px;width:451px}
.panel h2{position:absolute;top:30px;font-size:21px}
.panel p{position:absolute;top:62px;width:310px;font-size:8.5px;line-height:14.7px;color:#555}
.panel-report h2,.panel-report p,.panel-report .btn{left:130px}
.panel-view h2,.panel-view p,.panel-view .btn{left:25px}
.btn{position:absolute;top:115px;height:25px;padding:0 10px;display:flex;align-items:center;background:var(--navy);color:var(--white);font-size:10px;font-weight:600}

/* covered */
.covered-title{left:0;top:597px;width:903px;text-align:center;font-size:21px}
.covered-sub{left:0;top:632px;width:903px;text-align:center;font-size:8.5px;color:#555}
.feature{top:668px;width:190px;text-align:center}
.badge{margin:0 auto;width:134px;height:134px;border-radius:50%;background:#eceef1;padding:6px}
.badge-inner{width:122px;height:122px;border-radius:50%;background:linear-gradient(180deg,var(--blue),var(--navy-dark));display:flex;flex-direction:column;align-items:center;justify-content:center;gap:6px;color:var(--white);font-size:10px;font-weight:600}
.feature p{margin-top:10px;font-size:8.5px;line-height:14.7px;color:#555}
.feature .btn{position:static;display:inline-flex;margin-top:14px}

/* tabs */
.tabs{left:0;top:926px;width:903px;height:57px;background:var(--panel);border-top:1px solid var(--line);display:flex}
.tabs a{flex:1;display:flex;align-items:center;justify-content:center;font-size:14px;color:#222;border-right:1px solid var(--line)}
.tabs a:last-child{border-right:0}

/* footer */
.site-footer{left:0;top:983px;width:903px;height:217px;background:var(--footer);color:var(--footer-text)}
.site-footer .brand{left:130px;top:26px}
.site-footer .brand-mark{background:var(--red)}
.site-footer .brand-name{color:var(--white)}
.contact{left:130px;top:67px}
.contact strong{display:block;font-size:12px;color:var(--white);font-weight:600}
.contact span{font-size:8.5px}
.social{left:130px;top:114px;display:flex;gap:5px}
.social span{width:23px;height:23px;border-radius:50%;border:1.5px solid #c9ccd2}
.fcol{top:26px;font-size:8.5px;line-height:14.7px}
.fcol h3{font-size:10.5px;font-weight:600;color:var(--white);margin-bottom:7px}
.btn-agent{left:405px;top:1074px;width:106px;height:31px;background:var(--red);color:var(--white);display:flex;align-items:center;justify-content:center;gap:5px;font-size:10.5px;font-weight:600}
.legal{left:0;top:1141px;width:903px;text-align:center;font-size:8.5px;line-height:14.7px;color:var(--footer-text)}
</style>
</head>
<body>

<header class="site-header abs">
  <a class="brand abs" href="#"><span class="brand-mark"></span><span class="brand-name">HEARTHWARD<small>INSURANCE CO.</small></span></a>
  <nav class="main-nav abs">
    <a href="#">Home</a><a href="#">Insurance</a><a href="#">About Us</a><a href="#" class="active">Claims</a><a href="#">Agents</a><a href="#">Contact Us</a>
  </nav>
  <a class="btn-top btn-careers abs" href="#"><svg width="8" height="9" viewBox="0 0 8 9"><circle cx="4" cy="2.3" r="2.2" fill="#fff"/><path d="M0 9c0-3 1.8-4.2 4-4.2S8 6 8 9z" fill="#fff"/></svg>Careers</a>
  <a class="btn-top btn-login abs" href="#"><svg width="7" height="9" viewBox="0 0 7 9"><path d="M1.5 4V2.6a2 2 0 014 0V4" stroke="#fff" fill="none"/><rect y="4" width="7" height="5" rx="1" fill="#fff"/></svg>Login</a>
</header>

<section class="hero abs">
  <div class="hero-photo abs" role="img" aria-label="Photo of a man in a blazer working on a laptop by a bright window"></div>
  <h1>Claims Center</h1>
  <p>Accidents are stressful, but reporting and viewing your claim shouldn’t be. Whether you need to report a claim or check an existing one, Hearthward can help.</p>
</section>

<section class="panel panel-report abs">
  <h2>Report a Claim</h2>
  <p>Class aptent taciti sociosqu ad litora torquent per conubia nostra, per inceptos himenaeos. Mauris in erat justo. Nullam ac urna eu felis Sed non neque elit. massa nisl quis neque. Suspendisse in orci enim.</p>
  <a class="btn" href="#">Start The Claim Process</a>
</section>
<section class="panel panel-view abs">
  <h2>View a Claim</h2>
  <p>Class aptent taciti sociosqu ad litora torquent per conubia nostra, per inceptos himenaeos. Mauris in erat justo. Nullam ac urna eu felis Sed non neque elit. massa nisl quis neque. Suspendisse in orci enim.</p>
  <a class="btn" href="#">Login To My Policy</a>
</section>

<h2 class="covered-title abs">Home Owners has You Covered</h2>
<p class="covered-sub abs">The risk of damage to your home is why you have insurance in the first place. Hearthward is here to help you get your life back in order.</p>

<div class="feature abs" style="left:136px">
  <div class="badge"><div class="badge-inner">
    <svg width="36" height="32" viewBox="0 0 36 32" fill="#fff"><circle cx="18" cy="7" r="4"/><path d="M12 30V17a6 6 0 0112 0v13z"/><circle cx="6" cy="11" r="3"/><path d="M1 30V20a5 5 0 019 0v10z"/><circle cx="30" cy="11" r="3"/><path d="M26 30V20a5 5 0 019 0v10z"/></svg>
    Claims Team</div></div>
  <p>Class aptent taciti sociosqu ad litora justo. Nullam ac urna eu felis Sed non neque elit. massa nisl quis neque.</p>
  <a class="btn" href="#">Contact Our Claims Team</a>
</div>
<div class="feature abs" style="left:356px">
  <div class="badge"><div class="badge-inner">
    <svg width="30" height="34" viewBox="0 0 30 34" fill="none" stroke="#fff" stroke-width="2.5"><circle cx="15" cy="13" r="11"/><circle cx="15" cy="13" r="5" fill="#fff"/><path d="M8 22l-3 10 5-2 3 3 2-8M22 22l3 10-5-2-3 3-2-8"/></svg>
    Carrow Rated</div></div>
  <p>Class aptent taciti sociosqu ad litora justo. Nullam ac urna eu felis Sed non neque elit. massa nisl quis neque.</p>
</div>
<div class="feature abs" style="left:576px">
  <div class="badge"><div class="badge-inner">
    <svg width="38" height="34" viewBox="0 0 38 34"><circle cx="21" cy="15" r="14" fill="none" stroke="#fff" stroke-width="2.5"/><text x="21" y="20" text-anchor="middle" font-family="Source Sans 3,sans-serif" font-weight="700" font-size="13" fill="#fff">24</text><path d="M3 8c-3 5 1 16 12 24l4-5-4-4-3 2c-3-2-5-6-5-9l3-2-2-5z" fill="#fff"/></svg>
    24/7 Availability</div></div>
  <p>Class aptent taciti sociosqu ad litora justo. Nullam ac urna eu felis Sed non neque elit. massa nisl quis neque.</p>
</div>

<nav class="tabs abs">
  <a href="#">Claims FAQ</a><a href="#">About the Claims Process</a><a href="#">Report Fraud</a>
</nav>

<footer class="site-footer abs">
  <a class="brand abs" href="#"><span class="brand-mark"></span><span class="brand-name">HEARTHWARD<small>INSURANCE CO.</small></span></a>
  <div class="contact abs"><strong>1800 555 0142</strong><span>info@hearthwardinsurance.co</span></div>
  <div class="social abs" aria-label="Social links"><span></span><span></span><span></span><span></span></div>
  <div class="fcol abs" style="left:295px"><h3>Our Company</h3>Home<br>Insurance<br>About Us<br>Claims<br>Agents</div>
  <div class="fcol abs" style="left:404px"><h3>Login to Your Account</h3>Agents Login<br>Clients login</div>
  <div class="fcol abs" style="left:552px"><h3>Customer Support</h3>FAQs<br>Resources<br>Report a Claim<br>Find an Agent</div>
  <div class="fcol abs" style="left:679px"><h3>Connect With Us</h3>Support<br>Careers</div>
  <p class="legal abs">Copyright ©2018 Hearthward Insurance. All Rights Reserved<br>Terms of Use - Privacy Policy - Sitemap</p>
</footer>
<a class="btn-agent abs" href="#"><svg width="13" height="13" viewBox="0 0 13 13" fill="none" stroke="#fff" stroke-width="1.4"><circle cx="6" cy="6" r="4.8"/><path d="M9.5 9.5L12.5 12.5"/></svg>Find an Agent</a>

</body>
</html>
```